One of a kind service business!

We are the only ocean freight auditing company in the entire world that does what we do. We provide a innovative service in auditing our clients invoices for billing errors as it relates to the import and export of their products anywhere in the world. We'd like to retain the current logo - but we are open to any interesting concepts that can complete the card.

Target Market(s)

C-Level and Senior Financial executives

Industry/Entity Type

Auditing

Requirements
Must have

• ONE SIDED ONLY
Should not have
• no cartoonish images

```html
<!DOCTYPE html>
<html lang="en">
<head>
<meta charset="utf-8">
<title>Tidemark Review – Business Card</title>
<link href="https://fonts.googleapis.com/css2?family=Open+Sans:wght@400;700&display=swap" rel="stylesheet">
<style>
  :root {
    --page-bg: #e4e4e6;
    --card-white: #ffffff;
    --wave-blue: #1b6ea6;
    --deep-navy: #2b2360;
    --ink: #1f1f3a;
    --brand-blue: #1a79b4;
    --on-navy: #ffffff;
  }
  * { margin: 0; padding: 0; box-sizing: border-box; }
  html, body {
    width: 1200px; height: 944px; overflow: hidden;
    background: var(--page-bg);
    font-family: "Open Sans", Arial, sans-serif;
  }
  .card {
    position: absolute; left: 100px; top: 186px;
    width: 1000px; height: 572px;
    border-radius: 44px; overflow: hidden;
    background: var(--card-white);
    box-shadow: 0 10px 30px rgba(0,0,0,.25);
  }
  .card-waves { position: absolute; inset: 0; width: 100%; height: 100%; }
  .wave-band { fill: var(--wave-blue); }
  .navy-field { fill: var(--deep-navy); }

  .brand {
    position: absolute; left: 52px; top: 92px;
    display: flex; align-items: center; gap: 16px;
  }
  .brand-mark { width: 26px; height: 26px; background: var(--brand-blue); }
  .brand-name {
    font-size: 54px; font-weight: 700; color: var(--brand-blue);
    letter-spacing: 1px; line-height: 1;
  }

  .contact { position: absolute; left: 68px; color: var(--ink); font-size: 26px; line-height: 33px; }
  .address { top: 214px; }
  .lines { top: 329px; }
  .row { display: flex; align-items: flex-start; }
  .icon { width: 22px; height: 22px; margin: 6px 14px 0 0; flex: none; fill: var(--ink); }
  .address .text { display: block; }

  .holder {
    position: absolute; left: 700px; width: 250px; top: 452px;
    text-align: center; color: var(--on-navy);
  }
  .holder-name { font-size: 36px; line-height: 44px; }
  .holder-role { font-size: 24px; line-height: 32px; }
</style>
</head>
<body>
  <main class="card">
    <svg class="card-waves" viewBox="0 0 1000 572" preserveAspectRatio="none" aria-hidden="true">
      <path class="wave-band" d="M607 0 C690 110 660 210 600 310 C540 410 490 480 500 572 L1000 572 L1000 0 Z"/>
      <path class="navy-field" d="M690 0 C760 90 740 200 690 300 C640 400 585 480 590 572 L1000 572 L1000 0 Z"/>
    </svg>

    <div class="brand">
      <span class="brand-mark"></span>
      <span class="brand-name">Tidemark Review</span>
    </div>

    <div class="contact address">
      <div class="row">
        <svg class="icon" viewBox="0 0 22 22"><path d="M11 2 L21 11 H18 V20 H13 V14 H9 V20 H4 V11 H1 Z"/></svg>
        <div>
          <span class="text">Harbor Point Center</span>
          <span class="text">Lindenova 12, Brno</span>
          <span class="text">Czech Republic 60200</span>
        </div>
      </div>
    </div>

    <div class="contact lines">
      <div class="row">
        <svg class="icon" viewBox="0 0 22 22"><path d="M5 2 L9 2 L10 7 L7.5 9 C9 12.5 10 13.5 13 15 L15 12.5 L20 13.5 L20 17.5 C20 19 19 20 17.5 20 C9 19 3 13 2 4.5 C2 3 3 2 5 2 Z"/></svg>
        <span>+420 555 010 214</span>
      </div>
      <div class="row">
        <svg class="icon" viewBox="0 0 22 22"><path d="M7 1 H15 A2 2 0 0 1 17 3 V19 A2 2 0 0 1 15 21 H7 A2 2 0 0 1 5 19 V3 A2 2 0 0 1 7 1 Z M7 4 V15 H15 V4 Z"/></svg>
        <span>+420 555 020 387</span>
      </div>
      <div class="row">
        <svg class="icon" viewBox="0 0 22 22"><path d="M5 2 L9 2 L10 7 L7.5 9 C9 12.5 10 13.5 13 15 L15 12.5 L20 13.5 L20 17.5 C20 19 19 20 17.5 20 C9 19 3 13 2 4.5 C2 3 3 2 5 2 Z"/></svg>
        <span>+1 555 014 2290 - USA</span>
      </div>
      <div class="row">
        <svg class="icon" viewBox="0 0 22 22"><path d="M6 2 H14 L16 4 V8 H6 Z M2 9 H20 V18 H2 Z M5 12 H9 V14 H5 Z"/></svg>
        <span>+420 555 030 466</span>
      </div>
      <div class="row">
        <svg class="icon" viewBox="0 0 22 22"><circle cx="11" cy="11" r="10"/><path d="M1 11 H21 M11 1 C6 6 6 16 11 21 C16 16 16 6 11 1" stroke="#fff" stroke-width="1.4" fill="none"/></svg>
        <span>www.tidemarkreview.net</span>
      </div>
      <div class="row">
        <svg class="icon" viewBox="0 0 22 22"><path d="M1 5 H21 V18 H1 Z"/><path d="M1 5 L11 12 L21 5" stroke="#fff" stroke-width="1.6" fill="none"/></svg>
        <span>danielm@tidemarkreview.net</span>
      </div>
    </div>

    <div class="holder">
      <div class="holder-name">Daniel Moravec</div>
      <div class="holder-role">CEO</div>
    </div>
  </main>
</body>
</html>
```